Simple, High-Class Web Design Wanted - Motivational Speakers Site

1. Full Brief/Request & Specs outlined on following video -
http://clipvault-demo.com/watch/rTkWmaPzQb

2. Use colours, images as you feel suits objective (we are happy to pay up to US$30 for any good images but must have licence/permission).

3. Layout probably similar to existing site - www.podiumtalentgroup.com.au / http://podiumtalentgroup.com.au/contact.php

4. Must Be Able to Coded for MOBILE-FRIENDLINESS & WordPress friendly Ideal.

5. This is the first, small job of many we/graphic design jobs. If suits, winning designer may be offered all future work direct.

Thanks & look forward to your design. Glen.

Target Market(s)

corporates - high end

Number of Pages Required

2 page

Font styles to use
Sans Serif

Requirements
Must have
• Classy professional look
Nice to have
• all in Video in brief
Should not have
• too many images / new images I haven't approved

```html
<!DOCTYPE html>
<html lang="en">
<head>
<meta charset="utf-8">
<title>Speaker Name – Guest &amp; Keynote Speaker</title>
<link rel="stylesheet" href="https://fonts.googleapis.com/css2?family=Oswald:wght@300;400;500&family=Open+Sans:wght@400;600&display=swap">
<style>
  :root {
    --green: #5cb80f;
    --green-dark: #3f8f08;
    --charcoal: #1e1e1e;
    --charcoal-2: #2b2b2b;
    --band: #3a3a3a;
    --white: #ffffff;
    --text: #555555;
    --line: #8cc63f;
  }
  * { box-sizing: border-box; margin: 0; padding: 0; }
  html, body { width: 724px; height: 1200px; overflow: hidden; background: var(--white); }
  body { position: relative; font-family: "Open Sans", Arial, sans-serif; color: var(--text); }

  .hero {
    position: absolute; left: 0; top: 0; width: 724px; height: 414px;
    background: radial-gradient(ellipse at 65% 40%, #3a3a3a 0%, var(--charcoal) 70%);
    overflow: hidden;
  }
  .topbar {
    position: absolute; left: 48px; top: 0; width: 628px; height: 66px;
    background: var(--green); display: flex; align-items: center; padding: 0 14px;
    color: var(--white);
  }
  .brand { font-family: "Oswald", sans-serif; font-weight: 500; font-size: 27px; letter-spacing: 0.5px; }
  .topbar-contact { margin-left: auto; display: flex; gap: 22px; font-size: 15px; align-items: center; }
  .topbar-contact span { display: flex; align-items: center; gap: 7px; }
  .speaker-photo {
    position: absolute; right: 48px; top: 30px; width: 250px; height: 384px;
    background: linear-gradient(180deg, #555 0%, #2e2e2e 60%, #1a1a1a 100%);
    border-radius: 120px 120px 0 0;
  }
  .hero-headline {
    position: absolute; left: 48px; top: 112px; width: 410px;
    font-family: "Open Sans", Arial, sans-serif; font-weight: 400; font-size: 21px; line-height: 33px;
    color: var(--white); text-transform: uppercase;
  }
  .cta {
    position: absolute; left: 48px; top: 325px; width: 182px; height: 42px;
    background: var(--green); color: var(--white);
    font-family: "Oswald", sans-serif; font-size: 20px; text-transform: uppercase;
    display: flex; align-items: center; justify-content: center;
  }

  .welcome {
    position: absolute; left: 0; top: 414px; width: 724px; height: 70px;
    background: var(--band); color: var(--white);
    font-family: "Oswald", sans-serif; font-weight: 300; font-size: 32px;
    display: flex; align-items: center; justify-content: center; letter-spacing: 1px;
  }

  .video {
    position: absolute; left: 48px; top: 506px; width: 310px; height: 190px;
    background: linear-gradient(180deg, #dde2e6 0%, #a8b4c0 100%);
  }
  .video-bar { position: absolute; left: 0; bottom: 0; width: 100%; height: 16px; background: rgba(0,0,0,0.55); }
  .video-play { position: absolute; left: 135px; top: 75px; }
  .intro {
    position: absolute; left: 376px; top: 506px; width: 300px;
    font-size: 10.5px; line-height: 15px;
  }
  .intro p + p { margin-top: 14px; }

  .note-title {
    position: absolute; left: 48px; top: 748px; width: 628px;
    display: flex; align-items: center; gap: 18px;
    font-family: "Oswald", sans-serif; font-weight: 300; font-size: 34px; color: var(--green);
    letter-spacing: 2px;
  }
  .note-title::before, .note-title::after { content: ""; flex: 1; height: 1px; background: var(--line); }
  .notes { position: absolute; left: 68px; top: 815px; width: 600px; list-style: none; }
  .notes li { display: flex; align-items: center; gap: 22px; height: 62px; font-size: 10.5px; line-height: 15px; }
  .num {
    flex: none; width: 42px; height: 42px; border-radius: 50%;
    background: var(--green); color: var(--white); border: 3px solid #c9e6a8;
    font-family: "Oswald", sans-serif; font-size: 24px;
    display: flex; align-items: center; justify-content: center;
  }

  .contact-strip {
    position: absolute; left: 48px; top: 1012px; width: 628px; height: 94px;
    display: flex; background: var(--green); color: var(--white);
  }
  .contact-strip > div { flex: 1; display: flex; flex-direction: column; align-items: center; justify-content: center; gap: 8px; }
  .contact-form { background: var(--green-dark); font-family: "Oswald", sans-serif; font-size: 20px; text-transform: uppercase; text-align: center; line-height: 26px; }
  .contact-item { font-size: 14px; }
  .contact-item + .contact-item { border-left: 1px solid rgba(255,255,255,0.3); }

  .footer {
    position: absolute; left: 0; top: 1136px; width: 724px; height: 64px;
    background: var(--charcoal-2); color: var(--white);
    display: flex; align-items: center; padding: 0 48px; font-size: 10px;
  }
  .social { margin-left: auto; display: flex; gap: 10px; }
  .social span { width: 30px; height: 30px; border-radius: 50%; background: #111; display: block; }
  .social span:first-child { background: var(--green); }
</style>
</head>
<body>
  <header class="hero">
    <div class="speaker-photo" role="img" aria-label="Portrait of the speaker in a dark suit, arms crossed"></div>
    <div class="topbar">
      <div class="brand">SPEAKER NAME</div>
      <div class="topbar-contact">
        <span><svg width="16" height="16" viewBox="0 0 24 24" fill="#fff"><path d="M6.6 10.8a15 15 0 0 0 6.6 6.6l2.2-2.2a1 1 0 0 1 1-.25 11.4 11.4 0 0 0 3.6.57 1 1 0 0 1 1 1V20a1 1 0 0 1-1 1A17 17 0 0 1 3 4a1 1 0 0 1 1-1h3.5a1 1 0 0 1 1 1c0 1.25.2 2.45.57 3.57a1 1 0 0 1-.25 1z"/></svg>555 014 2290</span>
        <span><svg width="18" height="14" viewBox="0 0 24 18" fill="none" stroke="#fff" stroke-width="2"><rect x="1" y="1" width="22" height="16"/><path d="M1 1l11 9 11-9"/></svg>hello@keynotevoice.example</span>
      </div>
    </div>
    <h1 class="hero-headline">Are you looking for a guest or keynote speaker - inspiring, entertaining, industry expert etc, for a conference or special event?</h1>
    <a class="cta">Contact us now!</a>
  </header>

  <h2 class="welcome">WELCOME</h2>

  <div class="video" role="img" aria-label="Introductory video of the speaker">
    <svg class="video-play" width="40" height="40" viewBox="0 0 40 40"><circle cx="20" cy="20" r="19" fill="rgba(0,0,0,0.45)" stroke="#fff" stroke-width="2"/><path d="M16 12l12 8-12 8z" fill="#fff"/></svg>
    <div class="video-bar"></div>
  </div>
  <div class="intro">
    <p>Lorem Ipsum is simply dummy text of the printing and typesetting industry. Lorem Ipsum has been the industry's standard dummy text ever since the 1500s, when an unknown printer took a galley of type and scrambled it to make a type specimen book. It has survived not only five centuries, but also the leap into electronic typesetting, remaining essentially unchanged. It was popularised in the 1960s with the release of Letraset sheets containing Lorem Ipsum passages.</p>
    <p>Lorem Ipsum is simply dummy text of the printing and typesetting industry. Lorem Ipsum has been the industry's standard dummy text ever since the 1500s, when an unknown printer took a galley of type and scrambled it to make a type specimen book.</p>
  </div>

  <h2 class="note-title">PLEASE&nbsp; NOTE</h2>
  <ol class="notes">
    <li><span class="num">1</span>Lorem Ipsum is simply dummy text of the printing and typesetting industry. Lorem Ipsum has been the industry's standard dummy text ever since the 1500s.</li>
    <li><span class="num">2</span>Lorem Ipsum is simply dummy text of the printing and typesetting industry. Lorem Ipsum has been the industry's standard dummy text ever since the 1500s.</li>
    <li><span class="num">3</span>Lorem Ipsum is simply dummy text of the printing and typesetting industry. Lorem Ipsum has been the industry's standard dummy text ever since the 1500s.</li>
  </ol>

  <section class="contact-strip">
    <div class="contact-form">Quick<br>Contact Form</div>
    <div class="contact-item">
      <svg width="24" height="18" viewBox="0 0 24 18" fill="none" stroke="#fff" stroke-width="2"><rect x="1" y="1" width="22" height="16"/><path d="M1 1l11 9 11-9"/></svg>
      hello@keynotevoice.example
    </div>
    <div class="contact-item">
      <svg width="20" height="20" viewBox="0 0 24 24" fill="#fff"><path d="M6.6 10.8a15 15 0 0 0 6.6 6.6l2.2-2.2a1 1 0 0 1 1-.25 11.4 11.4 0 0 0 3.6.57 1 1 0 0 1 1 1V20a1 1 0 0 1-1 1A17 17 0 0 1 3 4a1 1 0 0 1 1-1h3.5a1 1 0 0 1 1 1c0 1.25.2 2.45.57 3.57a1 1 0 0 1-.25 1z"/></svg>
      555 014 2290
    </div>
  </section>

  <footer class="footer">
    <p>© <strong>SPEAKER NAME</strong> , 2015. All Rights Reserved.</p>
    <div class="social"><span></span><span></span><span></span></div>
  </footer>
</body>
</html>
```